business card deign

Logo needs the following on it.
1. attached logo
2. Tagline - "If it keeps a drink cold or the party going...we do it!"
3. Name- Dalton Pikes, Founder and CPO
4. Address - 412 E. Carver Avenue, Ste 2207, Tampa, FL. 33917
5. Phone - 555.318.4726

```html
<!DOCTYPE html>
<html lang="en">
<head>
<meta charset="utf-8">
<title>Boundra Business Card</title>
<link href="https://fonts.googleapis.com/css2?family=Montserrat:wght@400;700&display=swap" rel="stylesheet">
<style>
  :root {
    --backdrop: #3a3a3a;
    --card: #1c1c1c;
    --ink: #ffffff;
    --ink-soft: #d6d6d6;
    --rule: #8a8a8a;
  }
  * { box-sizing: border-box; margin: 0; padding: 0; }
  html, body { width: 1200px; height: 900px; overflow: hidden; }
  body {
    background: var(--backdrop);
    font-family: "Montserrat", Arial, sans-serif;
    color: var(--ink);
    position: relative;
  }
  .card {
    position: absolute;
    left: 250px;
    width: 700px;
    height: 400px;
    background: var(--card);
    box-shadow: 0 12px 30px rgba(0,0,0,.45);
  }
  .card--front { top: 40px; }
  .card--back { top: 460px; }

  .brand {
    display: flex;
    align-items: center;
    gap: 14px;
    font-weight: 700;
    font-size: 42px;
    letter-spacing: 10px;
    color: var(--ink);
  }
  .brand__dot {
    width: 22px; height: 22px;
    border-radius: 50%;
    background: var(--ink);
  }
  .card--front .brand {
    position: absolute;
    left: 0; right: 0; top: 150px;
    justify-content: center;
  }
  .tagline {
    position: absolute;
    left: 0; right: 0; bottom: 50px;
    text-align: center;
    font-size: 14px;
    color: var(--ink-soft);
    letter-spacing: .3px;
  }
  .card--back .brand {
    position: absolute;
    left: 50px; top: 175px;
  }
  .divider {
    position: absolute;
    left: 420px; top: 70px;
    width: 1px; height: 260px;
    background: var(--rule);
  }
  .contact {
    position: absolute;
    left: 445px; top: 78px;
    font-size: 14px;
    color: var(--ink-soft);
    line-height: 1.35;
  }
  .contact__name {
    font-size: 22px;
    font-weight: 700;
    color: var(--ink);
  }
  .contact__role { margin-bottom: 22px; }
  .contact__address { margin-bottom: 18px; }
  .contact__row {
    display: flex;
    align-items: center;
    gap: 10px;
    margin-bottom: 10px;
  }
  .contact__row svg { width: 14px; height: 14px; fill: var(--ink); }
</style>
</head>
<body>
  <section class="card card--front">
    <div class="brand"><span class="brand__dot"></span>BOUNDRA</div>
    <p class="tagline">If it keeps a drink cold or the party going...we do it</p>
  </section>

  <section class="card card--back">
    <div class="brand"><span class="brand__dot"></span>BOUNDRA</div>
    <div class="divider"></div>
    <div class="contact">
      <p class="contact__name">Dalton Pikes</p>
      <p class="contact__role">Founder and CPO</p>
      <p class="contact__address">412 E. Carver Avenue, Ste 2207,<br>Tampa, FL. 33917</p>
      <p class="contact__row">
        <svg viewBox="0 0 24 24" aria-hidden="true"><path d="M6.6 10.8a15.1 15.1 0 0 0 6.6 6.6l2.2-2.2c.3-.3.7-.4 1-.2 1.1.4 2.3.6 3.6.6.6 0 1 .4 1 1V20c0 .6-.4 1-1 1A17 17 0 0 1 3 4c0-.6.4-1 1-1h3.5c.6 0 1 .4 1 1 0 1.3.2 2.5.6 3.6.1.3 0 .7-.2 1z"/></svg>
        555.318.4726
      </p>
      <p class="contact__row">
        <svg viewBox="0 0 24 24" aria-hidden="true"><path d="M2 5h20v14H2zM4 7v.4l8 5 8-5V7z"/></svg>
        info@boundra.com
      </p>
      <p class="contact__row">
        <svg viewBox="0 0 24 24" aria-hidden="true"><circle cx="12" cy="12" r="10"/></svg>
        www.boundra.com
      </p>
    </div>
  </section>
</body>
</html>
```